Redesign This Psychology Website

We would like a slight redesign of this successful psychology (relationship counselling) website:

www.TheKelvaleClinic.com.au

We are updating the website, and we'd like a slight refresh of the design and style.

Please keep to very similar colours, and use the same logo. We're looking for around 10 page templates, however the main one is the home page.

Keep in mind, this website already converts quite well, so we want a new, fresh design in keeping with this one. Please don't bother designing something too extremely different.

thanks :)

Target Market(s)

couples who are looking for relationship counselling. Men and women, 25 - 70, across Australia

Industry/Entity Type

Psychology

Number of Pages Required

5+ page

Font styles to use
Sans Serif

Colors
87cfc6
b7a5cd
ec1f27
ffffff
cee9f5

Requirements
Must have
• a similar look to the current design, just looking for a slight refresh.
• Search bar
• Areas for lots of photos
• same logo
• lots of content areas
Nice to have
• great content areas, where we can display a lot of content and our areas.
Should not have
• no colors like orange, etc.
• should not have a totally different feel.

```html
<!DOCTYPE html>
<html lang="en">
<head>
<meta charset="utf-8">
<title>The Kelvale Clinic – Relationship Counselling</title>
<link href="https://fonts.googleapis.com/css2?family=Roboto:wght@300;400;500;700&display=swap" rel="stylesheet">
<style>
:root{
  --teal:#87cfc6;
  --teal-dark:#5fb8ad;
  --red:#ec1f27;
  --lilac:#b7a5cd;
  --sky:#cee9f5;
  --ink:#3f4a4c;
  --muted:#8a9496;
  --rule:#e4e8e9;
  --panel:#f4f6f7;
  --white:#ffffff;
}
*{box-sizing:border-box;margin:0;padding:0}
html,body{width:1200px;height:3197px;overflow:hidden}
body{font-family:'Roboto',sans-serif;color:var(--ink);background:var(--white);font-size:13px;line-height:1.9}
.page{position:relative;width:1200px;height:3197px}
.abs{position:absolute}
.ph{position:absolute;border-radius:0}

/* header */
.topbar{position:absolute;top:0;left:0;width:1200px;height:102px;border-top:4px solid var(--teal)}
.brand{position:absolute;display:flex;align-items:center;gap:10px}
.brand .dot{width:34px;height:34px;border-radius:50%;background:var(--teal)}
.brand .name{font-weight:500;color:var(--teal-dark);font-size:26px;line-height:1}
.brand small{display:block;font-size:10px;color:var(--teal-dark);font-weight:400;margin-top:4px}
.search{position:absolute;left:422px;top:34px;width:441px;height:36px;display:flex;border:1px solid var(--rule);border-radius:3px;overflow:hidden}
.search .field{flex:1;display:flex;align-items:center;gap:10px;padding-left:14px;color:#a5adaf;font-size:12px;background:#f7f8f8}
.search .btn{width:84px;background:var(--teal);color:#fff;font-size:12px;font-weight:500;display:flex;align-items:center;justify-content:center}
.call{position:absolute;left:886px;top:28px;display:flex;align-items:center;gap:12px;font-size:16px;color:var(--ink)}
.call .ring{width:46px;height:46px;border-radius:50%;background:var(--red);display:flex;align-items:center;justify-content:center}

.nav{position:absolute;top:102px;left:0;width:1200px;height:47px;background:var(--teal);display:flex;align-items:center}
.nav ul{list-style:none;display:flex;margin-left:128px}
.nav li{color:#fff;font-size:12px;font-weight:500;padding:0 30px;border-right:1px solid rgba(255,255,255,.45);line-height:14px}
.nav li:last-child{border-right:0}
.socials{position:absolute;left:886px;top:6px;display:flex;gap:9px}
.socials span{width:34px;height:34px;border-radius:50%;border:2px solid #fff}

/* hero */
.hero{position:absolute;top:149px;left:0;width:1200px;height:491px;background:linear-gradient(90deg,#f2f6f8 0%,#e8f1f5 50%,#dbe9ef 100%)}
.hero .photo{left:640px;top:0;width:560px;height:491px;background:linear-gradient(160deg,#e9f1f4 0%,#c4a590 45%,#4f8f9a 80%,#3d6f78 100%)}
.hero p{position:absolute;left:85px;top:370px;width:500px;font-size:12.5px;line-height:2.1;color:#4c5658}
.btn-red{position:absolute;background:var(--red);color:#fff;font-weight:500;font-size:14px;display:flex;align-items:center;justify-content:center;border-radius:3px}
.dots{position:absolute;left:85px;top:611px;display:flex;gap:6px}
.dots span{width:14px;height:14px;border-radius:50%;border:2px solid #b8c3c6}
.dots .on{border-color:var(--red)}

/* intro */
.eyebrow{font-size:16px;color:#6d7678;letter-spacing:.5px}
.headline{font-size:27px;color:var(--teal-dark);font-weight:500;letter-spacing:.5px}
.intro-text{font-size:12px;line-height:2.3;color:var(--muted)}

/* services */
.services{position:absolute;top:1066px;left:0;width:1200px;height:394px;background:var(--panel)}
.card{position:absolute;top:36px;width:247px}
.card .ph{position:relative;width:247px;height:160px}
.card h3{font-size:13px;color:var(--teal-dark);font-weight:500;margin-top:22px}
.card p{font-size:11.5px;line-height:2.1;color:var(--muted);margin-top:4px;height:70px}
.card .more{font-size:11px;color:var(--teal-dark);text-decoration:underline;margin-top:12px}

/* locations */
.band{position:absolute;top:1460px;left:0;width:1200px;height:369px;background:var(--teal);color:#fff}
.band h2{position:absolute;font-size:15px;font-weight:500;letter-spacing:.3px}
.band .lead{position:absolute;left:170px;top:74px;font-size:12px}
.loc{position:absolute;font-size:11.5px;line-height:30px;list-style:none}
.loc li::before{content:"▸";margin-right:20px;font-size:9px}
.divider{position:absolute;left:711px;top:40px;width:1px;height:290px;background:rgba(255,255,255,.5)}
.portrait{position:absolute;left:731px;top:106px;width:140px;height:140px;border-radius:50%;border:4px solid #fff;background:linear-gradient(160deg,#f5d58e,#e8b97a 60%,#6b9ca8)}
.quote{position:absolute;left:892px;top:100px;width:230px;font-size:11.5px;line-height:2.2}

/* blog */
.sec-title{position:absolute;width:1200px;text-align:center;font-size:26px;font-weight:300;color:#6d7678;letter-spacing:1px}
.sec-sub{position:absolute;width:1200px;text-align:center;font-size:11.5px;color:var(--muted)}
.post{position:absolute;top:1956px;width:331px}
.post .ph{position:relative;width:331px;height:196px}
.post h3{font-size:13px;color:var(--teal-dark);font-weight:500;margin-top:30px}
.post p{font-size:11.5px;line-height:2.2;color:var(--muted);margin-top:4px}
.post .meta{font-size:11.5px;color:var(--teal-dark);font-style:italic;margin-top:8px;display:flex;gap:24px}

/* partners */
.partners{position:absolute;top:2338px;left:0;width:1200px;height:187px;background:var(--panel)}
.badge{position:absolute;top:45px;width:173px;height:95px;background:#fff;border:1px solid var(--rule);display:flex;align-items:center;justify-content:center}
.badge span{width:110px;height:34px;border-radius:4px}
.chev{position:absolute;top:75px;font-size:34px;color:#d5dbdc;font-weight:300}

/* gallery */
.gal{position:absolute;top:2642px;height:171px}

/* footer */
.footer{position:absolute;top:2866px;left:0;width:1200px;height:266px;background:var(--panel)}
.footer h4{position:absolute;top:50px;font-size:14px;font-weight:500;color:#4c5658;letter-spacing:.5px}
.footer .txt{position:absolute;font-size:11.5px;line-height:2.1;color:var(--muted)}
.frow{display:flex;align-items:center;gap:14px;line-height:30px}
.email{position:absolute;left:632px;top:142px;width:214px;height:32px;border:1px solid #d6dcdd;background:#fff;font-size:11.5px;color:#6d7678;padding-left:12px;display:flex;align-items:center}
.ficons{position:absolute;left:898px;top:153px;display:flex;gap:8px}
.ficons span{width:34px;height:34px;border-radius:50%;border:2px solid #b8c3c6}
.copy{position:absolute;top:3132px;left:0;width:1200px;height:65px;background:var(--teal);color:#fff;font-size:11.5px;display:flex;align-items:center;justify-content:center}
</style>
</head>
<body>
<div class="page">

  <header class="topbar">
    <div class="brand" style="left:85px;top:16px">
      <span class="dot"></span>
      <div class="name">The Kelvale Clinic<small>helping you create loving relationships</small></div>
    </div>
    <div class="search">
      <div class="field">
        <svg width="13" height="13" viewBox="0 0 14 14"><circle cx="6" cy="6" r="4.5" fill="none" stroke="#8a9496" stroke-width="1.6"/><path d="M9.5 9.5l3.5 3.5" stroke="#8a9496" stroke-width="1.6"/></svg>
        <span>Enter Your Keyword ...</span>
      </div>
      <div class="btn">SEARCH</div>
    </div>
    <div class="call">
      <span class="ring"><svg width="20" height="20" viewBox="0 0 24 24"><path fill="#fff" d="M6.6 10.8a15 15 0 006.6 6.6l2.2-2.2c.3-.3.7-.4 1-.2 1.1.4 2.3.6 3.6.6.6 0 1 .4 1 1V20c0 .6-.4 1-1 1A17 17 0 013 4c0-.6.4-1 1-1h3.5c.6 0 1 .4 1 1 0 1.3.2 2.5.6 3.6.1.3 0 .7-.2 1z"/></svg></span>
      <span>CALL US : 1300 555 014</span>
    </div>
  </header>

  <nav class="nav">
    <ul>
      <li>HOME</li><li>ABOUT</li><li>RESOURCES</li><li>BLOG</li><li>SHOP</li><li>CART</li><li>CONTACT US</li>
    </ul>
    <div class="socials"><span></span><span></span><span></span><span></span><span></span></div>
  </nav>

  <section class="hero">
    <div class="ph photo" role="img" aria-label="Smiling couple embracing outdoors"></div>
    <div class="brand" style="left:85px;top:124px">
      <span class="dot" style="width:58px;height:58px"></span>
      <div class="name" style="font-size:38px">The Kelvale Clinic</div>
    </div>
    <p style="top:220px">At The Kelvale Clinic, we are a group of PSYCHOLOGISTS, Australia wide who are passionate about relationships and helping you with yours. Our vision is to provide regarded and comprehensive marriage counselling ...</p>
    <div class="btn-red" style="left:85px;top:320px;width:145px;height:43px">READ MORE</div>
    <div class="dots" style="top:462px"><span></span><span class="on"></span><span></span></div>
  </section>

  <section>
    <div class="ph" style="left:85px;top:686px;width:537px;height:328px;background:linear-gradient(120deg,#cfe3ea 0%,#e9c7a6 50%,#c99a7c 100%)" role="img" aria-label="Video still: clinic director speaking beside a smiling older couple"></div>
    <svg class="abs" style="left:315px;top:812px" width="78" height="78" viewBox="0 0 78 78"><circle cx="39" cy="39" r="36" fill="rgba(255,255,255,.25)" stroke="#fff" stroke-width="3"/><path d="M31 25l24 14-24 14z" fill="#fff"/></svg>
    <div class="abs eyebrow" style="left:667px;top:702px">WE SPECIALISE IN RELATIONSHIP</div>
    <div class="abs headline" style="left:667px;top:730px">MARRIAGE COUNSELLING</div>
    <p class="abs intro-text" style="left:667px;top:780px;width:450px">At The Kelvale Clinic, we are a group of PSYCHOLOGISTS, Australia wide who are passionate about relationships and helping you with yours. Our vision is to provide the most highly regarded and comprehensive marriage counselling and sex therapy in Australia, at reasonable and affordable rates.</p>
    <p class="abs intro-text" style="left:667px;top:890px;width:450px">When we are experiencing relationship and marriage problems, there can be a lot of pain and confusion, and it can often be difficult to cope with the other as are of our lives when we are struggling with problems with our partner. We are relationships and how to have a good one in our schools.</p>
  </section>

  <section class="services">
    <article class="card" style="left:85px">
      <div class="ph" style="background:linear-gradient(135deg,#d9c2ae,#b48c6e)" role="img" aria-label="Happy couple smiling together"></div>
      <h3>RELATIONSHIP COUNSELLING</h3>
      <p>Communication, Recovering from an affair, Loss of intimacy &amp; love, Power battles, Feeling like friends, not lovers</p>
      <div class="more">READ MORE</div>
    </article>
    <article class="card" style="left:347px">
      <div class="ph" style="background:linear-gradient(135deg,#e7d2c0,#c48f6c)" role="img" aria-label="Playful couple laughing"></div>
      <h3>SEX THERAPY COUNSELLING</h3>
      <p>Low libido , Erectile difficulties, Premature ejaculation, Differing libidos, Porn addiction, Keeping sex exciting</p>
      <div class="more">READ MORE</div>
    </article>
    <article class="card" style="left:607px">
      <div class="ph" style="background:linear-gradient(135deg,#c9b3a0,#7d5f4d)" role="img" aria-label="Frustrated man holding his head"></div>
      <h3>ANGER MANAGEMENT COUNSELLING</h3>
      <p>Managing angry outbursts, expressing your anger in healthy ways. Managing angry outbursts, expressing your anger</p>
      <div class="more">READ MORE</div>
    </article>
    <article class="card" style="left:867px">
      <div class="ph" style="background:linear-gradient(135deg,#f1ece8,#b89a88)" role="img" aria-label="Woman holding a white rose"></div>
      <h3>NARCISSISM COUNSELLING</h3>
      <p>Managing narcissistic, superior, entitled, arrogant and lack of empathy tendencies in you or your partner</p>
      <div class="more">READ MORE</div>
    </article>
  </section>

  <section class="band">
    <h2 style="left:127px;top:44px">OUR RELATIONSHIP COUNSELLING LOCATIONS ACROSS AUSTRALIA</h2>
    <div class="lead">We currently have relationship counselling and marriage counselling services in</div>
    <ul class="loc" style="left:127px;top:136px"><li>Sydney – 19 centres</li><li>Canberra – 2 centres</li><li>Melbourne – 21 centres</li><li>Perth – 12 centres</li><li>Brisbane – 14 centres</li></ul>
    <ul class="loc" style="left:322px;top:136px"><li>Wollongong – 1 centre</li><li>Central Coast – 2 centres</li><li>Adelaide – 4 centres</li><li>Gold Coast – 5 centres</li><li>Sunshine Coast – 2 centres</li></ul>
    <ul class="loc" style="left:539px;top:136px"><li>Cairns – 1 centre</li><li>Townsville – 1 centre</li><li>Wodonga – 1 centre</li></ul>
    <div class="divider"></div>
    <h2 style="left:743px;top:44px">OUR RELATIONSHIP COUNSELLING APPROACH</h2>
    <div class="portrait" role="img" aria-label="Portrait of the clinic director"></div>
    <div class="quote">So learning how to communicate your honest thoughts and feelings in a way that your partner does truly listen is a crucial skill for you to feel that you are in a fulfilling relationship. We can show you some simple but effective principles on how to do this with each other.
      <div style="margin-top:16px;font-size:10.5px;line-height:1.8">MAREN DOYLE<br>Director – Psychologist</div>
    </div>
  </section>

  <section>
    <h2 class="sec-title" style="top:1858px">LATEST BLOG</h2>
    <p class="sec-sub" style="top:1904px">Certain clinics also provide after hours and Saturday sessions for your convenience.</p>
    <article class="post" style="left:85px">
      <div class="ph" style="background:linear-gradient(135deg,#dcd6cf,#8f7766)" role="img" aria-label="Woman sitting thoughtfully on a sofa"></div>
      <h3>WHY AM I WITH A NARCISSIST?</h3>
      <p>Finding yourself in a "whirlwind romance", he/she will appear to be all you have ever wanted in a partner</p>
      <div class="meta"><span>February 24, 2017</span><span>05 Comments</span></div>
    </article>
    <article class="post" style="left:435px">
      <div class="ph" style="background:linear-gradient(135deg,#d3b7a4,#7a5a4b)" role="img" aria-label="Upset couple arguing"></div>
      <h3>HOW DO I KNOW IF I'M WITH A NARCISSIST?</h3>
      <p>However, our relationship with our partner is arguably the most important thing in our lives and actually</p>
      <div class="meta"><span>February 24, 2017</span><span>05 Comments</span></div>
    </article>
    <article class="post" style="left:784px">
      <div class="ph" style="background:linear-gradient(135deg,#cfd6da,#6b7f8c)" role="img" aria-label="Couple in a serious conversation"></div>
      <h3>RELATIONSHIP COUNSELLING</h3>
      <p>However, our relationship with our partner is arguably the most important thing in our lives and actually.</p>
      <div class="meta"><span>February 3, 2017</span><span>05 Comments</span></div>
    </article>
  </section>

  <section class="partners">
    <div class="chev" style="left:44px">‹</div>
    <div class="badge" style="left:111px"><span style="background:#2f8a4c"></span></div>
    <div class="badge" style="left:317px"><span style="background:#d9262e"></span></div>
    <div class="badge" style="left:522px"><span style="background:#1c5fa8"></span></div>
    <div class="badge" style="left:727px"><span style="background:#2ba6d8"></span></div>
    <div class="badge" style="left:932px"><span style="background:#4fa83d"></span></div>
    <div class="chev" style="left:1138px">›</div>
  </section>

  <section>
    <h2 class="sec-title" style="top:2552px">PHOTO GALLERY</h2>
    <p class="sec-sub" style="top:2596px">Certain clinics also provide after hours and Saturday sessions for your convenience.</p>
    <div class="gal" style="left:85px;width:200px;background:linear-gradient(135deg,#c48060,#7c4a3a)" role="img" aria-label="Couple embracing"></div>
    <div class="gal" style="left:292px;width:200px;background:linear-gradient(135deg,#e0cbb8,#9e7b64)" role="img" aria-label="Laughing couple"></div>
    <div class="gal" style="left:499px;width:200px;background:linear-gradient(135deg,#b6aaa0,#5d4b42)" role="img" aria-label="Couple talking at a café"></div>
    <div class="gal" style="left:706px;width:200px;background:linear-gradient(135deg,#e1c9b4,#b58d70)" role="img" aria-label="Couple sitting on a couch"></div>
    <div class="gal" style="left:913px;width:200px;background:linear-gradient(135deg,#c49a72,#6e5036)" role="img" aria-label="Couple dining together"></div>
    <div class="gal" style="left:1120px;width:-1px"></div>
    <div class="gal" style="left:913px;width:0"></div>
  </section>

  <footer class="footer">
    <div class="brand" style="left:105px;top:96px">
      <span class="dot" style="width:44px;height:44px"></span>
      <div class="name" style="font-size:24px">The Kelvale Clinic<small>helping you create loving relationships</small></div>
    </div>
    <h4 style="left:390px">CONTACT US</h4>
    <div class="txt" style="left:390px;top:90px">
      <div class="frow"><svg width="12" height="12" viewBox="0 0 12 12"><rect x="1" y="1" width="10" height="10" rx="2" fill="#8a9496"/></svg>1300 555 014 (Phone)</div>
      <div class="frow"><svg width="12" height="12" viewBox="0 0 12 12"><rect x="1" y="3" width="10" height="7" fill="#8a9496"/></svg>1300 555 015 (Fax)</div>
      <div class="frow" style="color:var(--teal-dark);text-decoration:underline"><svg width="12" height="12" viewBox="0 0 12 12"><rect x="1" y="2" width="10" height="8" fill="none" stroke="#8a9496" stroke-width="1.5"/><path d="M1 2l5 4 5-4" stroke="#8a9496" fill="none"/></svg>info@thekelvaleclinic.com.au</div>
      <div class="frow" style="align-items:flex-start;line-height:20px;margin-top:5px"><svg width="12" height="14" viewBox="0 0 12 14"><path d="M6 0a5 5 0 015 5c0 4-5 9-5 9S1 9 1 5a5 5 0 015-5z" fill="#8a9496"/></svg><span>#24 Lorem Ipsum Dummy<br>Lorem Ipsum</span></div>
    </div>
    <h4 style="left:632px">NEWSLETTER</h4>
    <p class="txt" style="left:632px;top:88px;width:230px">Register Your email address to get information about us</p>
    <div class="email">Email Address</div>
    <div class="btn-red" style="left:632px;top:192px;width:82px;height:28px;font-size:10px;border-radius:2px">SUBSCRIBE</div>
    <h4 style="left:898px">FOLLOW US</h4>
    <p class="txt" style="left:898px;top:88px;width:210px">Lorem ipsum dolor sit amet, conse ctetur adipiscing elit. Nulla in purus nibh. Donec ornare</p>
    <div class="ficons"><span></span><span></span><span></span><span></span><span></span></div>
  </footer>

  <div class="copy">© Copyright 2017 The Kelvale Clinic All Rights Reserved</div>
</div>
</body>
</html>
```